Dental Office Needs Exciting New Stationary

We need a stationary design that incorporates the logo that we already have and would like to keep the existing color scheme. We need something clean and professional. This is a Endodontic (root canals) office and must represent a dental specialist's office. I need a design for a business card, envelope, and letterhead that all coordinate. I would like the business card to incorporate the information in the business card sample that I am providing. I made the business card design myself but would like to see a better one.
Dental

```html
<!DOCTYPE html>
<html lang="en">
<head>
<meta charset="utf-8">
<title>Summit Endodontics Stationery</title>
<link href="https://fonts.googleapis.com/css2?family=Open+Sans:wght@400;600;700&display=swap" rel="stylesheet">
<style>
  :root {
    --backdrop: #2e2e2e;
    --paper: #ffffff;
    --brand-blue: #1f6fc4;
    --deep-blue: #2546a8;
    --sky-blue: #2a9be0;
    --swoosh-gray: #a9abb0;
    --text-gray: #555a60;
    --faint-mark: #eef1f7;
    --window-gray: #e6e7e9;
  }
  * { box-sizing: border-box; margin: 0; padding: 0; }
  html, body { width: 1200px; height: 900px; overflow: hidden; }
  body {
    background: var(--backdrop);
    font-family: "Open Sans", Arial, sans-serif;
    position: relative;
    color: var(--text-gray);
  }
  .piece {
    position: absolute;
    background: var(--paper);
    overflow: hidden;
  }
  .wave { position: absolute; left: 0; bottom: 0; width: 100%; display: block; z-index: 1; }
  .site {
    position: absolute;
    color: #fff;
    font-size: 10px;
    z-index: 2;
  }
  .brand {
    position: absolute;
    display: flex;
    align-items: center;
    gap: 9px;
    color: var(--brand-blue);
    font-weight: 700;
    white-space: nowrap;
    line-height: 1.05;
    z-index: 2;
  }
  .brand-dot {
    border-radius: 50%;
    border: 3px solid var(--brand-blue);
    flex: none;
  }
  .contact {
    position: absolute;
    display: flex;
    font-size: 9.5px;
    line-height: 12px;
    color: var(--text-gray);
    z-index: 2;
  }
  .contact b { color: var(--brand-blue); font-weight: 600; }
  .contact-col { padding-right: 14px; border-right: 1px solid #ccc; white-space: nowrap; }
  .contact-col:last-child { border-right: none; padding-left: 14px; padding-right: 0; }
  .faint-mark {
    position: absolute;
    border-radius: 50%;
    background: var(--faint-mark);
    z-index: 0;
  }

  /* Letterhead */
  .letterhead { left: 28px; top: 66px; width: 506px; height: 752px; }
  .letterhead .brand { left: 40px; top: 46px; font-size: 19px; }
  .letterhead .brand-dot { width: 34px; height: 34px; }
  .letterhead .contact { left: 262px; top: 46px; }
  .letterhead .faint-mark { left: 72px; top: 214px; width: 360px; height: 360px; }
  .letterhead .wave { height: 60px; }
  .letterhead .site { left: 46px; bottom: 12px; }

  /* Business card front */
  .card-front { left: 580px; top: 138px; width: 287px; height: 162px; }
  .card-front .brand { left: 64px; top: 28px; font-size: 14px; gap: 7px; }
  .card-front .brand-dot { width: 24px; height: 24px; border-width: 2px; }
  .card-front .people {
    position: absolute; left: 0; right: 0; top: 82px;
    text-align: center; font-size: 7.5px; line-height: 10px;
    color: var(--deep-blue); font-weight: 700;
  }
  .card-front .people span { color: var(--text-gray); font-weight: 400; }
  .card-front .details {
    position: absolute; left: 0; right: 0; top: 106px;
    text-align: center; font-size: 6px; line-height: 8.5px;
  }
  .card-front .details b { color: var(--brand-blue); font-weight: 600; }
  .card-front .wave { height: 26px; }
  .card-front .site { left: 24px; bottom: 3px; font-size: 7px; }

  /* Business card back */
  .card-back {
    left: 881px; top: 135px; width: 287px; height: 163px;
    background: linear-gradient(135deg, var(--sky-blue) 0%, var(--brand-blue) 45%, var(--deep-blue) 100%);
  }
  .card-back .faint-mark { left: 70px; top: -30px; width: 160px; height: 160px; background: rgba(255,255,255,0.07); }
  .card-back .brand { left: 48px; top: 52px; font-size: 21px; color: #fff; gap: 11px; }
  .card-back .brand-dot { width: 40px; height: 40px; border-color: #fff; }
  .card-back .site { left: 0; right: 0; bottom: 9px; text-align: center; font-size: 7.5px; }

  /* Envelope front */
  .envelope-front { left: 582px; top: 323px; width: 585px; height: 255px; }
  .envelope-front .brand { left: 34px; top: 36px; font-size: 17px; }
  .envelope-front .brand-dot { width: 32px; height: 32px; }
  .envelope-front .contact { left: 336px; top: 32px; font-size: 8.5px; line-height: 11px; }
  .envelope-front .faint-mark { left: 385px; top: 60px; width: 190px; height: 190px; }
  .address-window {
    position: absolute; left: 34px; top: 129px; width: 202px; height: 50px;
    border: 1px solid #b9bbbe; border-radius: 6px;
    background: linear-gradient(#f7f7f8, var(--window-gray));
    z-index: 2;
  }
  .envelope-front .wave { height: 58px; }
  .envelope-front .site { left: 44px; bottom: 10px; font-size: 9px; }

  /* Envelope back */
  .envelope-back { left: 582px; top: 601px; width: 585px; height: 254px; }
  .envelope-back .flap { position: absolute; left: 0; top: 0; width: 100%; height: 86px; }
  .envelope-back .flap-dot {
    position: absolute; left: 268px; top: 18px; width: 48px; height: 48px;
    border-radius: 50%; border: 3px solid #fff;
  }
  .envelope-back .back-site {
    position: absolute; left: 0; right: 0; bottom: 18px;
    text-align: center; font-size: 10px; color: var(--text-gray); letter-spacing: 0.5px;
  }
  .envelope-back .back-site b { color: var(--brand-blue); font-weight: 400; }
</style>
</head>
<body>

<svg width="0" height="0" style="position:absolute">
  <defs>
    <linearGradient id="band-blue" x1="0" x2="1" y1="0" y2="0">
      <stop offset="0" stop-color="#2546a8"/>
      <stop offset="0.5" stop-color="#2a9be0"/>
      <stop offset="1" stop-color="#2546a8"/>
    </linearGradient>
    <linearGradient id="flap-blue" x1="0" x2="1" y1="0" y2="1">
      <stop offset="0" stop-color="#2546a8"/>
      <stop offset="0.5" stop-color="#2a9be0"/>
      <stop offset="1" stop-color="#2546a8"/>
    </linearGradient>
  </defs>
</svg>

<!-- Letterhead -->
<section class="piece letterhead">
  <div class="faint-mark" role="img" aria-label="Faint background brand emblem"></div>
  <div class="brand"><span class="brand-dot"></span><span class="brand-name">Summit<br>Endodontics</span></div>
  <div class="contact">
    <div class="contact-col"><b>O</b> : 555.201.3400<br><b>F</b> : 555.201.3401<br>2480 Elm Street<br>Riverton, CA 95010</div>
    <div class="contact-col"><b>O</b> : 555.348.7700<br><b>F</b> : 555.348.7701<br>410 Oak Avenue Suite #2<br>Fairview, CA 95120</div>
  </div>
  <svg class="wave" viewBox="0 0 506 60" preserveAspectRatio="none">
    <path d="M0,26 C160,6 330,28 506,0 L506,8 C330,36 160,16 0,32 Z" fill="var(--swoosh-gray)"/>
    <path d="M0,36 C170,18 340,40 506,14 L506,60 L0,60 Z" fill="url(#band-blue)"/>
  </svg>
  <div class="site">www.summitendodontics.com</div>
</section>

<!-- Business card front -->
<section class="piece card-front">
  <div class="brand"><span class="brand-dot"></span><span class="brand-name">Summit<br>Endodontics</span></div>
  <div class="people">Daniel R Moreland <span>| DDS MS</span><br>Marco L Ortega <span>| DDS</span></div>
  <div class="details">
    <b>O</b> : 555.201.3400 | <b>F</b> : 555.201.3401 | <b>O</b> : 555.348.7700 | <b>F</b> : 555.348.7701<br>
    2480 Elm Street Riverton, CA 95010<br>
    410 Oak Avenue Suite #2 Fairview, CA 95120
  </div>
  <svg class="wave" viewBox="0 0 287 26" preserveAspectRatio="none">
    <path d="M0,12 C90,4 180,14 287,0 L287,5 C180,18 90,8 0,16 Z" fill="var(--swoosh-gray)"/>
    <path d="M0,18 C95,9 190,19 287,7 L287,26 L0,26 Z" fill="url(#band-blue)"/>
  </svg>
  <div class="site">www.summitendodontics.com</div>
</section>

<!-- Business card back -->
<section class="piece card-back">
  <div class="faint-mark" role="img" aria-label="Faint background brand emblem"></div>
  <div class="brand"><span class="brand-dot"></span><span class="brand-name">Summit<br>Endodontics</span></div>
  <div class="site">www.summitendodontics.com</div>
</section>

<!-- Envelope front -->
<section class="piece envelope-front">
  <div class="faint-mark" role="img" aria-label="Faint background brand emblem"></div>
  <div class="brand"><span class="brand-dot"></span><span class="brand-name">Summit<br>Endodontics</span></div>
  <div class="contact">
    <div class="contact-col"><b>O</b> : 555.201.3400<br><b>F</b> : 555.201.3401<br>2480 Elm Street<br>Riverton, CA 95010</div>
    <div class="contact-col"><b>O</b> : 555.348.7700<br><b>F</b> : 555.348.7701<br>410 Oak Avenue Suite #2<br>Fairview, CA 95120</div>
  </div>
  <div class="address-window"></div>
  <svg class="wave" viewBox="0 0 585 58" preserveAspectRatio="none">
    <path d="M0,28 C180,4 380,30 585,6 L585,16 C380,40 180,14 0,34 Z" fill="var(--swoosh-gray)"/>
    <path d="M0,38 C190,14 390,40 585,20 L585,58 L0,58 Z" fill="url(#band-blue)"/>
  </svg>
  <div class="site">www.summitendodontics.com</div>
</section>

<!-- Envelope back -->
<section class="piece envelope-back">
  <svg class="flap" viewBox="0 0 585 86" preserveAspectRatio="none">
    <path d="M0,0 L585,0 L585,6 C560,10 450,40 330,76 C310,84 275,84 255,76 C135,40 25,10 0,6 Z" fill="url(#flap-blue)"/>
  </svg>
  <div class="flap-dot"></div>
  <div class="back-site">www.<b>summitendodontics</b>.com</div>
</section>

</body>
</html>
```